Cozy Cradle Loops Needs a Beautiful Website

I need a new website for this new E-commerce. I sell handmade baby crochets, e.g. booties, headbands, hats, etc. I need a feminine and soft design to make the moms-to-be say 'oohh ahh'. I'd like pink, blue and gray. I'd like an inviting homepage, and nice regular pages where people can see and order the products.

Industry/Entity Type

Baby

Requirements
Must have
• beautiful, soft, feminine design. Please use pictures of the colors I'd like: brown, yellow, pink and blue. Any combination, but definitely include brown.

```html
<!DOCTYPE html>
<html lang="en">
<head>
<meta charset="utf-8">
<title>Cozy Cradle Loops – Handmade Baby Crochets</title>
<link rel="stylesheet" href="https://fonts.googleapis.com/css2?family=Noto+Serif:ital,wght@0,700;1,700&family=PT+Sans:wght@400;700&display=swap">
<style>
:root{
  --brown:#4a2f22;
  --brown-dark:#2e1c14;
  --pink:#e4307f;
  --pink-dark:#c81d68;
  --blue:#1aa6cf;
  --blue-dark:#0b8db6;
  --ink:#333;
  --muted:#555;
  --line:#e2e2e2;
  --white:#fff;
}
*{box-sizing:border-box;margin:0;padding:0}
html,body{width:1200px;height:1181px;overflow:hidden}
body{background:var(--brown);font-family:"PT Sans",sans-serif;color:var(--ink);position:relative}
.floor{position:absolute;left:0;top:1136px;width:1200px;height:45px;background:var(--brown-dark)}
.page{position:absolute;left:218px;top:0;width:768px;height:1087px;background:var(--white)}
.abs{position:absolute}
.logo{left:28px;top:18px;font:700 26px/1 "PT Sans",sans-serif;color:var(--pink)}
.cart{left:546px;top:20px;width:208px;height:26px;border:1px solid #ccc;box-shadow:0 1px 2px rgba(0,0,0,.15);font-size:9px;display:flex;align-items:center;padding:0 20px;justify-content:space-between}
.cart b{font-weight:400;color:#111}.cart b span{color:var(--pink)}.cart a{color:var(--blue);text-decoration:none}
.nav{left:12px;top:72px;width:742px;height:31px;background:var(--pink);display:flex;align-items:center}
.nav a{font:italic 700 12px "Noto Serif",serif;color:#fff;text-decoration:none;padding:0 17px;height:31px;line-height:31px}
.nav a.active{background:var(--blue);padding:0 16px}
.search{position:absolute;right:12px;top:4px;width:186px;height:23px;background:#fff;border-radius:12px;font-size:10px;color:#999;padding-left:11px;line-height:23px}
.search span{position:absolute;right:0;top:0;width:30px;height:23px;background:#e8e8e8;border-radius:0 12px 12px 0;color:#333;font-weight:700;text-align:center}
.hero{left:12px;top:117px;width:742px;height:249px;border-radius:4px;overflow:hidden;background:linear-gradient(90deg,#2a1a14 0%,#6b3a22 25%,#b7703a 45%,#7b8fb3 70%,#9fb2d2 100%)}
.hero-photo{position:absolute;right:0;top:0;width:330px;height:249px;background:radial-gradient(ellipse at 50% 55%,#f1cdb3 0%,#d8a68c 40%,rgba(160,175,210,0) 75%)}
.hero h1{position:absolute;left:34px;top:28px;font:italic 700 42px "Noto Serif",serif;color:var(--pink)}
.hero h2{position:absolute;left:34px;top:90px;font:400 15px "Noto Serif",serif;color:#fff;text-transform:uppercase}
.hero p{position:absolute;left:34px;top:118px;width:320px;font-size:11.5px;line-height:18px;color:#fff}
.btn-shop{position:absolute;left:33px;top:191px;width:94px;height:29px;background:var(--blue);border-radius:3px;font:italic 700 13px/29px "Noto Serif",serif;color:#fff;text-align:center;box-shadow:0 2px 3px rgba(0,0,0,.3)}
.dots{position:absolute;right:20px;top:231px;display:flex;gap:4px}
.dots i{width:6px;height:6px;border-radius:50%;background:#fff}.dots i:first-child{background:var(--pink)}
.box{left:12px;width:139px;background:linear-gradient(#fff,#eee);border:1px solid #e6e6e6;border-radius:3px;box-shadow:0 6px 6px -5px rgba(0,0,0,.2)}
.box h3{font:italic 700 11px "Noto Serif",serif;color:#444;margin:11px 0 10px 11px}
.box li{list-style:none;font-size:9px;color:#444;line-height:18px;padding-left:14px}
.box li.more{color:var(--blue)}
.price li{padding-left:21px}
.discount{left:12px;top:668px;width:139px;height:170px;border-radius:3px;overflow:hidden}
.discount .ph{height:132px;background:linear-gradient(160deg,#cfe3f2,#e9d3c6 60%,#f3ece8)}
.discount .tag{height:38px;background:var(--pink);font:italic 700 14px/38px "Noto Serif",serif;color:#fff;padding-left:11px}
.band{left:162px;width:592px;height:27px;background:linear-gradient(var(--blue),var(--blue-dark));border-radius:3px 3px 0 0;font:700 12px/27px "Noto Serif",serif;color:#fff;padding-left:10px}
.card{width:140px;height:177px;border:1px solid var(--line);background:#fff}
.card .name{font-size:9px;color:var(--blue-dark);position:absolute;left:10px;top:7px}
.card .ph{position:absolute;left:8px;top:22px;width:124px;height:124px}
.card .cost{position:absolute;left:7px;top:155px;font:700 11.5px "Noto Serif",serif;color:#111}
.card .buy{position:absolute;right:7px;top:150px;width:65px;height:19px;background:linear-gradient(#ef4a92,var(--pink-dark));border-radius:3px;font:italic 700 10px/19px "Noto Serif",serif;color:#fff;text-align:center;box-shadow:0 1px 2px rgba(0,0,0,.3)}
.welcome{left:165px;top:862px;font:700 13px "Noto Serif",serif;color:var(--blue);text-transform:uppercase}
.mosaic{left:166px;top:895px;width:153px;height:108px;background:linear-gradient(135deg,#8a3b3b,#3c4960 40%,#c8b89e 70%,#2d4a5c)}
.about{left:330px;top:891px;width:416px;font-size:8.6px;line-height:16.5px;color:#333;text-align:justify}
.footer{left:12px;top:1042px;width:742px;height:29px;background:var(--pink);display:flex;align-items:center;padding-left:24px}
.footer a{font:italic 700 9.6px "Noto Serif",serif;color:#fff;text-decoration:none}
.footer .sep{color:#fff;font-size:9px;margin:0 7px}
.social{position:absolute;right:34px;top:9px;display:flex;gap:8px}
.social i{width:11px;height:11px;border-radius:50%;background:#fff}
</style>
</head>
<body>
<div class="floor"></div>
<main class="page">
  <div class="abs logo">Cozy Cradle Loops</div>
  <div class="abs cart"><b>Shopping Cart: <span>0 items</span></b><a href="#">View cart</a></div>

  <nav class="abs nav">
    <a class="active" href="#">Home</a><a href="#">About Us</a><a href="#">New Arrials</a><a href="#">Baby Crochets</a><a href="#">Blog</a><a href="#">Contact</a>
    <div class="search">Search<span>GO</span></div>
  </nav>

  <section class="abs hero">
    <div class="hero-photo" role="img" aria-label="Two babies wearing crocheted crowns sitting on a soft rug"></div>
    <h1>New Arrials</h1>
    <h2>Dolor sit amet, consectetur adipiscing elit.</h2>
    <p>Ut metus felis, posuere ac eleifend eget, tristique id magna. In iaculis pellentesque nisl vel blandit. Phasellus ac orci eget mi malesuada varius ac quis purus.</p>
    <div class="btn-shop">Shop Now</div>
    <div class="dots"><i></i><i></i><i></i><i></i></div>
  </section>

  <aside class="abs box" style="top:379px;height:151px">
    <h3>Shop by Category</h3>
    <ul><li>Crochets</li><li>Booties</li><li>Headbands,</li><li>Hats</li><li class="more">More</li></ul>
  </aside>
  <aside class="abs box price" style="top:542px;height:112px">
    <h3>Shop by Price</h3>
    <ul><li>Under $25</li><li>$25 - $50</li><li>$50 - $100</li><li>Over $100</li></ul>
  </aside>
  <aside class="abs discount">
    <div class="ph" role="img" aria-label="Sleeping baby in a blue knitted hat on white fur"></div>
    <div class="tag">Exclusive Discount</div>
  </aside>

  <div class="abs band" style="top:379px">FEATURED PRODUCTS</div>
  <div class="abs card" style="left:162px;top:416px"><span class="name">Product #001</span><div class="ph" role="img" aria-label="Pink crocheted crown" style="background:radial-gradient(#ff8cc0,#f3dde6 70%)"></div><span class="cost">$78.88</span><span class="buy">Buy Now</span></div>
  <div class="abs card" style="left:313px;top:416px"><span class="name">Product #002</span><div class="ph" role="img" aria-label="Pale pink crocheted ballet booties" style="background:radial-gradient(#f4b8c8,#e6e0da 70%)"></div><span class="cost">$18.88</span><span class="buy">Buy Now</span></div>
  <div class="abs card" style="left:464px;top:416px"><span class="name">Product #003</span><div class="ph" role="img" aria-label="Turquoise crocheted booties" style="background:radial-gradient(#3fb3c8,#2a6f7e 80%)"></div><span class="cost">$24.88</span><span class="buy">Buy Now</span></div>
  <div class="abs card" style="left:615px;top:416px"><span class="name">Product #004</span><div class="ph" role="img" aria-label="Light blue crocheted crown" style="background:radial-gradient(#6fd7ea,#eef2f3 70%)"></div><span class="cost">$111.00</span><span class="buy">Buy Now</span></div>

  <div class="abs band" style="top:626px">OUR PRODUCTS</div>
  <div class="abs card" style="left:162px;top:662px"><span class="name">Product #005</span><div class="ph" role="img" aria-label="Gray crocheted booties with red flowers" style="background:radial-gradient(#9a9a9a,#5b5e62 80%)"></div><span class="cost">$78.88</span><span class="buy">Buy Now</span></div>
  <div class="abs card" style="left:313px;top:662px"><span class="name">Product #006</span><div class="ph" role="img" aria-label="Red crocheted booties" style="background:radial-gradient(#d0302c,#5a4b48 85%)"></div><span class="cost">$36.88</span><span class="buy">Buy Now</span></div>
  <div class="abs card" style="left:464px;top:662px"><span class="name" style="left:15px">Product #003</span><div class="ph" role="img" aria-label="Magenta crocheted crown" style="background:radial-gradient(#f07ad8,#eef0f0 70%)"></div><span class="cost">$85.00</span><span class="buy">Buy Now</span></div>
  <div class="abs card" style="left:615px;top:662px"><span class="name">Product #003</span><div class="ph" role="img" aria-label="Brown crocheted sneaker booties with pink star" style="background:radial-gradient(#7a6a60,#b58ab4 90%)"></div><span class="cost">$14.88</span><span class="buy">Buy Now</span></div>

  <h2 class="abs welcome">Welcome to Cozy Cradle Loops</h2>
  <div class="abs mosaic" role="img" aria-label="Collage of crocheted baby sneakers in red, gray, pink, yellow and blue"></div>
  <p class="abs about">Consectetur adipisicing elit, sed do eiusmod tempor incididunt ut labore et dolore magna aliqua. Ut enim ad minim veniam, quis nostrud exercitation ullamco laboris nisi ut aliquip ex ea commodo consequat. Duis aute irure dolor in reprehenderit in voluptate velit esse cillum dolore eu fugiat nulla pariatur. Excepteur sint occaecat cupidatat non proident, sunt in culpa qui officia deserunt mollit anim id est laborum.Consectetur adipisicing elit, sed do eiusmod tempor incididunt ut labore et dolore magna aliqua. Ut enim ad minim veniam, quis nostrud exercitation ullamco laboris nisi ut aliquip ex ea commodo consequat. Duis aute irure dolor in reprehenderit in voluptate velit</p>

  <footer class="abs footer">
    <a href="#">Home</a><span class="sep">I</span><a href="#">About Us</a><span class="sep">I</span><a href="#">New Arrials</a><span class="sep">I</span><a href="#">Baby Crochets</a><span class="sep">I</span><a href="#">Blog</a><span class="sep">I</span><a href="#">Contact</a>
    <div class="social" aria-label="Social links"><i></i><i></i><i></i><i></i></div>
  </footer>
</main>
</body>
</html>
```